Two Marketing Brochures

We need two professional A4 brochures (PDF + web version) to promote our new handyman services to Facility Managers in Queensland.
Brochure 1: Brightmoor Property Care Trade Services (see content Brightmoor Property Care.pdf). Create new cover page and contents page then design 2 content pages (left and right) I will then paste all text myself, rather than designing 19 pages.
Brochure 2: Brightmoor Property Care Minor Works & Maintenance – Quicker, Tidier, Leaner
Audience: Commercial property managers, Tarrow Gov, councils, schools, industrial clients
Style: Clean, modern, corporate, Brightmoor Property Care-branded
Content: Text is finalised and ready to go
Deliverables: A4 PDF (print-ready) + web version (compressed)
Optional: Integration of JobNest elements (e.g. “Book Now” QR or icon)

```html
<!DOCTYPE html>
<html lang="en">
<head>
<meta charset="utf-8">
<title>Brightmoor Property Care – Trade Services Catalogue</title>
<link href="https://fonts.googleapis.com/css2?family=Lexend:wght@300;400;500;600&family=Red+Hat+Display:wght@700;900&display=swap" rel="stylesheet">
<style>
  :root{
    --backdrop:#e4e4e4;
    --navy:#1f4a78;
    --navy-deep:#14375f;
    --cyan:#22e4f2;
    --ink:#1c3250;
    --text:#3b4250;
    --blue:#1761b2;
    --paper:#ffffff;
    --panel:#f2f2f3;
    --rule:#9fb0c4;
    --white:#ffffff;
  }
  *{box-sizing:border-box;margin:0;padding:0}
  html,body{width:850px;height:1200px;overflow:hidden}
  body{background:var(--backdrop);font-family:"Lexend",sans-serif;color:var(--text);position:relative}
  .spread{position:absolute;left:50px;width:750px;height:533px;display:flex}
  .spread--cover{top:51px}
  .spread--inside{top:616px}
  .page{position:relative;width:375px;height:100%;overflow:hidden}
  .page--cover{background:linear-gradient(160deg,#24548a 0%,var(--navy) 45%,var(--navy-deep) 100%);color:var(--white)}
  .page--light{background:var(--paper)}
  .abs{position:absolute}
  .center-x{left:0;right:0;text-align:center}
  .brand{font-weight:500;font-size:19px;letter-spacing:.01em;color:var(--white)}
  .photo{position:absolute;border-radius:4px}
  .photo--harbour{left:52px;top:46px;width:288px;height:150px;background:linear-gradient(180deg,#2b5a8e 0%,#8fa3b8 55%,#1d3f66 100%);opacity:.8}
  .photo--bathroom{left:21px;top:111px;width:340px;height:189px;background:linear-gradient(120deg,#3a5577 0%,#2a3e58 50%,#3f6a5a 100%);opacity:.85}
  .contact-icon{width:16px;height:16px;left:50%;margin-left:-8px;fill:var(--cyan)}
  .phone{font-weight:600;font-size:22px}
  .contact-line{font-weight:300;font-size:16px}
  .cover-title{font-family:"Red Hat Display",sans-serif;font-weight:900;font-size:50px;line-height:43px;letter-spacing:-.01em}
  .cover-sub{color:var(--cyan);font-size:24px;letter-spacing:.33em;font-weight:400}
  .rule{position:absolute;height:1px;background:rgba(255,255,255,.6)}
  .cover-topics{font-weight:300;font-size:16px;line-height:21px}

  .charge-band{position:absolute;left:0;top:0;width:375px;height:103px;background:var(--panel)}
  .eyebrow{font-size:17px;letter-spacing:.2em;color:var(--ink);font-weight:400}
  .headline{font-family:"Red Hat Display",sans-serif;font-weight:900;color:var(--ink)}
  .vline{position:absolute;width:1px;background:var(--blue)}
  .intro{font-size:10px;line-height:12.5px;color:var(--ink);font-weight:400}
  .mode-label{font-size:11px;color:var(--blue);font-weight:500}
  .mode-label--dark{color:var(--ink)}
  .mode-title{font-size:18px;line-height:17px;font-weight:500;color:var(--ink)}
  .mode-title--blue{color:var(--blue)}
  .mode-copy{font-size:8.3px;line-height:10.2px;font-weight:300;color:var(--text)}
  .product{position:absolute;border-radius:6px}
  .product--radiator{left:236px;top:134px;width:141px;height:97px;background:linear-gradient(180deg,#fafafa,#dcdcdc)}
  .product--heater{left:34px;top:266px;width:105px;height:110px;background:linear-gradient(180deg,#2b2b30 0%,#c65a22 50%,#2b2b30 100%)}

  .overview-eyebrow{font-size:14px;letter-spacing:.2em;color:var(--ink)}
  .service-title{font-size:16px;font-weight:500;color:var(--blue)}
  .service-sub{font-size:12px;font-weight:300;color:var(--blue)}
  .hrule{position:absolute;height:1px;background:var(--rule)}
  .box{position:absolute;background:var(--panel);border:1px solid #b8c6d6}
  .block-title{font-size:15px;font-weight:400;color:var(--ink);margin-bottom:4px}
  .block-lead{font-size:7px;line-height:9px;color:var(--ink);margin-bottom:3px}
  .ticks{list-style:none}
  .ticks li{position:relative;padding-left:8px;font-size:6.9px;line-height:8.8px;font-weight:300;color:var(--text);margin-bottom:3.2px}
  .ticks li::before{content:"↗";position:absolute;left:0;top:0;color:var(--blue);font-size:7px;font-weight:600}
  .ticks strong{font-weight:500}
</style>
</head>
<body>

<section class="spread spread--cover">
  <div class="page page--cover">
    <div class="photo photo--harbour" role="img" aria-label="Night view of a harbourside opera house seen through large stylised letters"></div>
    <div class="abs center-x brand" style="top:232px">Brightmoor Property Care</div>
    <svg class="abs contact-icon" style="top:310px" viewBox="0 0 24 24" aria-hidden="true"><path d="M6.6 10.8a15.1 15.1 0 0 0 6.6 6.6l2.2-2.2a1 1 0 0 1 1-.25 11.4 11.4 0 0 0 3.6.57 1 1 0 0 1 1 1V20a1 1 0 0 1-1 1A17 17 0 0 1 3 4a1 1 0 0 1 1-1h3.5a1 1 0 0 1 1 1c0 1.25.2 2.45.57 3.57a1 1 0 0 1-.25 1z"/></svg>
    <div class="abs center-x phone" style="top:335px">1300 555 019</div>
    <svg class="abs contact-icon" style="top:377px;height:13px" viewBox="0 0 24 18" aria-hidden="true"><path d="M0 0h24v2.5L12 10 0 2.5z"/><path d="M0 5l12 7.5L24 5v13H0z"/></svg>
    <div class="abs center-x contact-line" style="top:396px">hello@brightmoorcare.com.au</div>
    <svg class="abs contact-icon" style="top:428px;margin-left:-4px" viewBox="0 0 24 24" aria-hidden="true"><path d="M4 2l15 10-6.5 1.5L16 21l-3 1.3-3.4-7.6L4 19z"/></svg>
    <div class="abs center-x contact-line" style="top:448px">brightmoorpropertycare.com.au</div>
  </div>

  <div class="page page--cover">
    <div class="abs center-x brand" style="top:52px">Brightmoor Property Care</div>
    <div class="photo photo--bathroom" role="img" aria-label="Dark modern bathroom with freestanding bath and forest window seen through large stylised letters"></div>
    <div class="abs center-x cover-title" style="top:300px">TRADE<br>SERVICES</div>
    <div class="abs center-x cover-sub" style="top:388px;padding-left:.33em">CATALOGUE</div>
    <div class="rule" style="left:72px;width:226px;top:435px"></div>
    <div class="abs center-x cover-topics" style="top:442px">Appliances, Plumbing,<br>Electrical, Heating &amp; Cooling</div>
    <div class="rule" style="left:72px;width:226px;top:492px"></div>
  </div>
</section>

<section class="spread spread--inside">
  <div class="page page--light">
    <div class="charge-band"></div>
    <div class="abs eyebrow" style="left:42px;top:33px">HOW WE</div>
    <div class="abs headline" style="left:41px;top:50px;font-size:27px">CHARGE</div>
    <div class="vline" style="left:160px;top:23px;height:64px"></div>
    <p class="abs intro" style="left:174px;top:40px;width:180px">We have simplified charging to 3 different modes - so you always have control over your costs.</p>

    <div class="abs mode-label" style="left:26px;top:147px">Mode 01</div>
    <div class="vline" style="left:78px;top:132px;height:45px"></div>
    <div class="abs mode-title" style="left:88px;top:137px">Do &amp;<br>Change</div>
    <div class="product product--radiator" role="img" aria-label="White panel radiator"></div>
    <p class="abs mode-copy" style="left:27px;top:186px;width:192px">This is when nobody is sure what a problem is and what needs to be done. Think of it as a general service, where we send a plumber, electrician, or heating &amp; cooling specialist to site and attempt to make repairs, whatever they are.</p>

    <div class="product product--heater" role="img" aria-label="Compact black fan heater with glowing element"></div>
    <div class="abs mode-label mode-label--dark" style="left:153px;top:270px">Mode 02</div>
    <div class="vline" style="left:205px;top:255px;height:44px"></div>
    <div class="abs mode-title mode-title--blue" style="left:216px;top:259px">Flat Rate<br>Service</div>
    <p class="abs mode-copy" style="left:154px;top:310px;width:193px">In the following pages, we have listed our standard services with a fixed price. This way, you will know exactly what you will pay for these services, and they are exactly as described. If there is any variation or addition to these costs, we will not proceed without authorised approval.</p>

    <div class="abs mode-label" style="left:26px;top:402px">Mode 03</div>
    <div class="vline" style="left:78px;top:393px;height:37px"></div>
    <div class="abs mode-title" style="left:88px;top:401px">Quote</div>
    <p class="abs mode-copy" style="left:27px;top:437px;width:236px">Where a job can be clearly scoped, &amp; no additional technical information is required, we will provide a free quote for your consideration. We will attend the site and take negotiated measurements. If a fault-finding or technical assessment is required on-site before a quote is submitted, then we will need to attend as a 'do and charge.'</p>
  </div>

  <div class="page page--light">
    <div class="abs center-x overview-eyebrow" style="top:28px;padding-left:.2em">SERVICE OVERVIEW</div>
    <div class="abs center-x headline" style="top:46px;font-size:22px">ELECTRICAL</div>
    <div class="hrule" style="left:93px;width:172px;top:77px"></div>
    <div class="abs center-x service-title" style="top:80px">Appliance Inspection</div>
    <div class="abs center-x service-sub" style="top:98px">(Electrical, Gas, Water)</div>
    <div class="hrule" style="left:93px;width:172px;top:120px"></div>

    <div class="box" style="left:7px;top:134px;width:162px;height:144px;padding:7px 8px 0 10px">
      <div class="block-title">Works Include</div>
      <ul class="ticks">
        <li>Testing &amp; diagnosis of appliance issue.</li>
        <li>Minor repairs where economical to do so.</li>
        <li>Report detailing the appliance issue or repairs made.</li>
        <li>Quotation for replacement of appliance if beyond reasonable &amp; practical repair.</li>
        <li><strong>Photos</strong> before and after.</li>
        <li>Removal &amp; disposal of all rubbish works.</li>
        <li>Area cleaned upon completion of work.</li>
      </ul>
    </div>
    <div class="abs" style="left:181px;top:132px;width:174px">
      <div class="block-title" style="font-size:12.5px;margin-bottom:2px">Important Notes</div>
      <ul class="ticks">
        <li>To test &amp; work on appliances, all appliances must be readily accessible. If we must wait an extended time for an appliance to become accessible to test (e.g., someone is using the appliance, or an oven is too hot to work on), additional hourly charges will be incurred.</li>
        <li>All appliances/equipment must be reasonably accessible and in a clean environment. Example: Technicians cannot move dirty/clean dishes or laundry to access an appliance. Technicians require clear access to an appliance &amp; clean working area.</li>
        <li>No responsibility is taken for goods damaged while working. if they are not moved in preparation for the technician to complete their work.</li>
      </ul>
    </div>

    <div class="hrule" style="left:83px;width:205px;top:314px"></div>
    <div class="abs center-x service-title" style="top:318px">Electrical Safety Inspection</div>
    <div class="hrule" style="left:83px;width:205px;top:342px"></div>

    <div class="abs" style="left:17px;top:360px;width:124px">
      <div class="block-title" style="margin-bottom:1px">Works Include</div>
      <p class="block-lead">Testing of all accessible parts of the electrical installation, including</p>
      <ul class="ticks">
        <li>Visual inspection.</li>
        <li>Mandatory testing in accordance with AS/NZS:3019:2022.</li>
        <li>Audit report showing compliance and/or defect list.</li>
        <li><strong>Photos</strong> before and after.</li>
        <li>Removal and disposal of all rubbish related to works.</li>
        <li>Area cleaned upon completion of work.</li>
      </ul>
    </div>
    <div class="box" style="left:173px;top:356px;width:188px;height:163px;padding:4px 8px 0 8px">
      <div class="block-title" style="font-size:12.5px;margin-bottom:2px">Important Notes</div>
      <ul class="ticks">
        <li>If any part of the electrical installation is found to present clear and immediate danger to property or persons, then we will disconnect that appliance or part of the installation from supply and quote for remedial works later.</li>
        <li>All parts of the installation and equipment must be reasonably accessible and in a clean environment. Example: Technicians cannot crawl under renters' tables or around/over furniture to access light fixtures, power outlets, smoke alarms, nor can we be expected to move dirty dishes/glasses/appliances, etc., to access appliances.</li>
        <li>Power must be connected to the property.</li>
      </ul>
    </div>
  </div>
</section>

</body>
</html>
```